Liron Vasek Website

Website for my son who is in 7th grade in the US. This will prepare him to show people his accomplishments when applying for a job or going to college. It should have:
* A picture (or multiple pictures)
* A resume page
* A place to share your accomplishments
* Links to his other social profiles
* A contact form

Great to include:
* Internships (show some photos of it along with what you’ve learned).
* Volunteer work.
* A side hustle that you want to highlight

Website sample I like:
https://belinamorud.sitefolio-demo.com/belinamorudtavik

Target Market(s)

For jobs and colleges admissions.

Number of Pages Required

5+ page

Colors

Designer to choose colors to be used in the design.

Requirements
Must have
• * A picture (or multiple pictures)
• * A resume page
• * A place to share your accomplishments
• * Links to his other social profiles
• * A contact form
Nice to have
• Great to include:
• * Internships (show some photos of it along with what you’ve learned).
• * Volunteer work.
• * A side hustle that you want to highlight

```html
<!DOCTYPE html>
<html lang="en">
<head>
<meta charset="utf-8">
<title>Liron Vasek</title>
<link href="https://fonts.googleapis.com/css2?family=Noto+Sans:wght@700;800&family=Open+Sans:wght@400;600&display=swap" rel="stylesheet">
<style>
:root{
  --orange:#ff6a00;
  --ink:#141414;
  --body:#555;
  --light:#f1f1f1;
  --dark:#3b3b3b;
  --white:#fff;
  --line:#6a6a6a;
}
*{box-sizing:border-box;margin:0;padding:0}
html,body{width:1200px;height:4250px;overflow:hidden}
body{font-family:"Open Sans",sans-serif;color:var(--body);background:var(--white);position:relative}
.heading{font-family:"Noto Sans",sans-serif;font-weight:800;color:var(--ink);text-align:center;letter-spacing:.5px}
.btn{display:inline-block;background:var(--orange);color:var(--white);font-family:"Noto Sans",sans-serif;font-weight:700;text-align:center;text-decoration:none}

/* header */
.site-header{height:109px;display:flex;align-items:center;padding:0 88px}
.brand{font-family:"Noto Sans",sans-serif;font-weight:800;font-size:46px;color:#2a2a2a;width:367px}
.nav{display:flex;gap:0}
.nav a{font-size:17px;color:#222;text-decoration:none;margin-right:47px}
.nav a.active{color:var(--orange)}

/* hero */
.hero{position:relative;height:582px;background:linear-gradient(90deg,#5a4a3e 0%,#8a7a6c 35%,#b09a88 55%,#8d8a86 75%,#5e5d5a 100%)}
.hero-copy{position:absolute;left:87px;top:170px;width:380px}
.hero-copy h1{font-family:"Noto Sans",sans-serif;font-weight:800;font-size:60px;color:var(--white);line-height:1}
.hero-copy p{color:#f2ece6;font-size:18px;line-height:30px;margin-top:26px}
.hero-copy .outline{display:inline-block;margin-top:26px;border:2px solid var(--orange);color:var(--white);font-family:"Noto Sans",sans-serif;font-weight:700;font-size:17px;padding:12px 26px;text-decoration:none}

/* about */
.about{height:543px;text-align:center;padding-top:56px}
.about h2{font-size:48px}
.about p{width:960px;margin:36px auto 0;font-size:18px;line-height:36px}
.about .btn{margin-top:48px;width:330px;height:65px;line-height:65px;font-size:23px}

/* accomplishments */
.accomplishments{height:703px;background:var(--light);text-align:center;padding-top:46px;position:relative}
.accomplishments h2{font-size:44px}
.accomplishments .lead{font-size:18px;line-height:29px;color:#333;width:720px;margin:22px auto 0}
.timeline{position:absolute;top:218px;height:434px;border-left:1.5px solid var(--line)}
.timeline.left{left:142px}.timeline.right{left:661px}
.entry{position:absolute;left:55px;width:349px;background:var(--white);border-left:3px solid var(--orange);text-align:left;padding:12px 0 14px 13px}
.entry::before{content:"";position:absolute;left:-58px;top:37px;width:55px;border-top:1.5px solid var(--line)}
.entry::after{content:"";position:absolute;left:-65px;top:30px;width:11px;height:11px;border:2px solid var(--orange);border-radius:50%;background:var(--white)}
.entry h3{font-family:"Noto Sans",sans-serif;font-weight:700;font-size:20px;color:var(--ink)}
.entry .meta{font-size:14px;margin-top:6px}
.entry p{font-size:14px;line-height:18px;margin-top:6px;padding-right:4px}

/* internships */
.internships{height:663px;background:var(--orange);text-align:center;padding-top:50px;color:var(--white)}
.internships h2{color:var(--white);font-size:42px}
.internships .lead{font-size:17px;line-height:27px;width:800px;margin:22px auto 0}
.intern-grid{display:flex;justify-content:space-between;width:976px;margin:60px auto 0}
.intern-card{width:266px}
.intern-photo{height:192px;border:3px solid var(--white);background:linear-gradient(135deg,#c9b8a4,#8e9aa8 60%,#e7e3dc)}
.intern-card h3{font-family:"Noto Sans",sans-serif;font-weight:700;font-size:25px;margin-top:14px}
.intern-card p{font-size:15px;line-height:29px;margin-top:8px}

/* volunteer */
.volunteer{height:622px;position:relative}
.volunteer-photo{position:absolute;left:91px;top:93px;width:372px;height:437px;background:linear-gradient(160deg,#f1d9a8 0%,#d2a774 45%,#8c8372 80%,#4e5563 100%)}
.volunteer-copy{position:absolute;left:542px;top:90px;width:570px}
.volunteer-copy h2{text-align:left;font-size:44px}
.volunteer-copy p{font-size:19px;line-height:36px;margin-top:28px;color:#444}
.volunteer-copy .btn{margin-top:38px;width:282px;height:64px;line-height:64px;font-size:22px}

/* contact */
.contact{height:601px;background:#f3f3f3;text-align:center;padding-top:38px}
.contact h2{font-size:42px}
.contact .lead{font-size:17px;line-height:27px;width:910px;margin:24px auto 0}
.contact-form{width:944px;margin:36px auto 0;display:grid;grid-template-columns:1fr 1fr;gap:14px 24px;text-align:left}
.field{height:40px;border:1px solid #ccc;background:var(--white);font:13px "Open Sans",sans-serif;padding:0 12px;color:#444}
.field.message{grid-column:1/3;height:115px;padding-top:14px;resize:none}
.contact .btn{margin-top:55px;width:214px;height:57px;border:0;font-size:23px}

/* footer */
.site-footer{height:427px;background:var(--dark);color:var(--white);text-align:center;padding-top:48px}
.site-footer .heading{color:var(--white);font-size:40px}
.footer-info{margin-top:30px;border-top:1px solid #555;border-bottom:1px solid #555;height:140px;display:flex;align-items:center;padding:0 90px;justify-content:space-between;font-size:19px}
.info{display:flex;align-items:center;gap:20px;text-align:center;line-height:22px}
.social{display:flex;justify-content:center;gap:14px;margin-top:32px}
.social span{width:38px;height:38px;border:2px solid var(--white);border-radius:50%}
.copyright{font-size:16px;margin-top:34px}
</style>
</head>
<body>

<header class="site-header">
  <div class="brand">Liron Vasek</div>
  <nav class="nav">
    <a class="active" href="#">Home</a><a href="#">Portfolio</a><a href="#">Resume</a><a href="#">Achievements</a><a href="#">Blog</a><a href="#">Contact</a>
  </nav>
</header>

<section class="hero" role="img" aria-label="Portrait of a smiling young student with a backpack in a school hallway">
  <div class="hero-copy">
    <h1>Liron Vasek.</h1>
    <p>Lorem ipsum dolor sit amet, consectetur adipiscing elit. Nullam hendrerit sollicitudin condimentum. Etiam malesuada ut tortor non dictum.</p>
    <a class="outline" href="#">VIEW MORE</a>
  </div>
</section>

<section class="about">
  <h2 class="heading">ABOUT ME</h2>
  <p>Lorem ipsum dolor sit amet, consectetur adipiscing elit. Nullam hendrerit sollicitudin condimentum. Etiam malesuada ut tortor non dictum. Pellentesque sollicitudin nibh nec tristique faucibus. Sed sit amet facilisis nisi. Duis et felis dictum, venenatis lectus eu, luctus arcu. Praesent viverra eros in leo suscipit, sed volutpat nunc auctor. Aenean scelerisque, urna nec laoreet laoreet, ligula massa tempus mauris, nec placerat lectus felis in justo. Sed erat magna, tristique et porttitor eget, eleifend sit amet mi. Cras id vestibulum ipsum. Nulla facilisi. Aenean blandit sem velit, non interdum lorem mattis vel. Maecenas iaculis felis neque, sit amet lobortis ante sodales vel.</p>
  <a class="btn" href="#">VIEW FULL RESUME</a>
</section>

<section class="accomplishments">
  <h2 class="heading">ACCOMPLISHMENTS</h2>
  <p class="lead">Lorem ipsum dolor sit amet, consectetur adipiscing elit. Nullam hendrerit sollicitudin condimentum. Etiam malesuada ut tortor non dictum</p>
  <div class="timeline left">
    <article class="entry" style="top:33px"><h3>Lorem Ipsum</h3><div class="meta">2012&nbsp; Northfield Labs</div><p>Lorem ipsum dolor sit amet, consectetur adipiscing elit. Nullam hendrerit sollicitudin condimentum. Etiam malesuada ut tortor non dictum.</p></article>
    <article class="entry" style="top:226px"><h3>Lorem Ipsum</h3><div class="meta">2015&nbsp; Northfield Labs</div><p>Lorem ipsum dolor sit amet, consectetur adipiscing elit. Nullam hendrerit sollicitudin condimentum. Etiam malesuada ut tortor non dictum.</p></article>
  </div>
  <div class="timeline right">
    <article class="entry" style="top:33px"><h3>Lorem Ipsum</h3><div class="meta">2016&nbsp; Northfield Labs</div><p>Lorem ipsum dolor sit amet, consectetur adipiscing elit. Nullam hendrerit sollicitudin condimentum. Etiam malesuada ut tortor non dictum.</p></article>
    <article class="entry" style="top:226px"><h3>Lorem Ipsum</h3><div class="meta">2018&nbsp; Northfield Labs</div><p>Lorem ipsum dolor sit amet, consectetur adipiscing elit. Nullam hendrerit sollicitudin condimentum. Etiam malesuada ut tortor non dictum.</p></article>
  </div>
</section>

<section class="internships">
  <h2 class="heading">INTERSHIPS</h2>
  <p class="lead">Lorem ipsum dolor sit amet, consectetur adipiscing elit. Nullam hendrerit sollicitudin condimentum. Etiam malesuada ut tortor non dictum. Pellentesque sollicitudin nibh nec tristique faucibus.</p>
  <div class="intern-grid">
    <div class="intern-card"><div class="intern-photo" role="img" aria-label="Two students working together at a laptop"></div><h3>Lorem Ipsum</h3><p>Lorem ipsum dolor sit amet, consectetur adipiscing elit. Nullam hendrerit sollicitudin condimentum. Etiam malesuada ut tortor non</p></div>
    <div class="intern-card"><div class="intern-photo" role="img" aria-label="Group of interns gathered around laptops"></div><h3>Lorem Ipsum</h3><p>Lorem ipsum dolor sit amet, consectetur adipiscing elit. Nullam hendrerit sollicitudin condimentum. Etiam malesuada ut tortor non</p></div>
    <div class="intern-card"><div class="intern-photo" role="img" aria-label="Three colleagues reviewing work on a laptop"></div><h3>Lorem Ipsum</h3><p>Lorem ipsum dolor sit amet, consectetur adipiscing elit. Nullam hendrerit sollicitudin condimentum. Etiam malesuada ut tortor non</p></div>
  </div>
</section>

<section class="volunteer">
  <div class="volunteer-photo" role="img" aria-label="Volunteers stacking hands together in sunlight"></div>
  <div class="volunteer-copy">
    <h2 class="heading">VOLUNTEER</h2>
    <p>Lorem ipsum dolor sit amet, consectetur adipiscing elit. Nullam hendrerit sollicitudin condimentum. Etiam malesuada ut tortor non dictum. Pellentesque sollicitudin nibh nec tristique faucibus. Sed sit amet facilisis nisi. Duis et felis dictum, venenatis lectus eu, luctus arcu. Praesent viverra eros in leo suscipit, sed volutpat nunc auctor. Aenean scelerisque, urna nec laoreet laoreet, ligula massa tempus mauris,</p>
    <a class="btn" href="#">VIEW VOLUNTEER</a>
  </div>
</section>

<section class="contact">
  <h2 class="heading">CONTACT US</h2>
  <p class="lead">Lorem ipsum dolor sit amet, consectetur adipiscing elit. Ut quis viverra tortor. Nunc luctus ornare arcu, at pulvinar mauris. Sed libero eros, consequat sed aliquam quis, placerat eu risus.</p>
  <form class="contact-form">
    <input class="field" placeholder="Name"><input class="field" placeholder="Email">
    <input class="field" placeholder="Phone Number"><input class="field" placeholder="Appointments">
    <textarea class="field message" placeholder="Messages"></textarea>
  </form>
  <button class="btn" type="button">SUBMIT</button>
</section>

<footer class="site-footer">
  <div class="heading">LIRON VASEK</div>
  <div class="footer-info">
    <div class="info">
      <svg width="32" height="32" viewBox="0 0 32 32" aria-hidden="true"><rect width="32" height="32" rx="4" fill="#fff"/><path d="M10 7l4 4-2 3c1 3 3 5 6 6l3-2 4 4-3 3C14 25 7 18 7 10z" fill="#3b3b3b"/></svg>
      <span>555 01 2468</span>
    </div>
    <div class="info">
      <svg width="20" height="28" viewBox="0 0 20 28" aria-hidden="true"><path d="M10 0a10 10 0 0 1 10 10c0 7-10 18-10 18S0 17 0 10A10 10 0 0 1 10 0z" fill="#fff"/><circle cx="10" cy="10" r="4" fill="#3b3b3b"/></svg>
      <span>Flat 12 Harlow Row,<br>Westbrook, KT4 2LP</span>
    </div>
    <div class="info">
      <svg width="30" height="22" viewBox="0 0 30 22" aria-hidden="true"><rect width="30" height="22" rx="2" fill="#fff"/><path d="M1 2l14 11L29 2" stroke="#3b3b3b" stroke-width="2" fill="none"/></svg>
      <span>info@lironvasek.com</span>
    </div>
  </div>
  <div class="social">
    <span aria-label="Social profile link"></span><span aria-label="Social profile link"></span><span aria-label="Social profile link"></span><span aria-label="Social profile link"></span>
  </div>
  <p class="copyright">Copyright © 2019&nbsp; Liron Vasek. All rights reserved</p>
</footer>

</body>
</html>
```